tinyTally Resource Book - 10 maths tasks to do outside

I need a 22 (11 pages back to back) page A6 sized book produced to standard for submission to professional printer. Needs to be as .pdf file showing guide lines and allowances for colour bleed. I have text already written and submitted as attachment in a Word file with margins set to A6 size. The theme of the materials is "Nature Play" so using lots of pictures from nature (Australia preferably) and showing lots of patterns in nature (rocks, leaves, flower petals etc). Some of the tasks refer to specific activities, such as "shadows" and "floating" so would be great to illustrate appropriately. The big emphasis is on learning outside the classroom, getting kids to engage actively with nature. I would like to see the pages as full colour - so not white background. The book itself will be spiral bound along the top edge so a margin of at least 1cm will be required at the top of each page (or the bottom of even numbered pages). Book will be printed on plastic laminated matte paper for outdoor use. Font size needs to be big enough to read. Fonts sizes, alignments and page numbers are all different at the moment and need to be standardised. One photo is included in a page as a sample if you can use it, otherwise disregard. Logo for Wattlebrook Numeracy Guild is also included to have as part of the acknowledgements at the back of the book.

Target Market(s)

Book is for early childhood and preschool teachers.

Industry/Entity Type

Education

Font styles to use
Sans Serif

Requirements
Must have
• Colour and appeal.
Nice to have
• Use of natural colours instead of bright catchy colours but that is your call.
Should not have
• American spelling

```html
<!DOCTYPE html>
<html lang="en-AU">
<head>
<meta charset="utf-8">
<title>Same Same Different</title>
<link rel="stylesheet" href="https://fonts.googleapis.com/css2?family=Poppins:wght@700&family=Mulish:ital,wght@1,900&family=Didact+Gothic&display=swap">
<style>
  :root {
    --paper: #ffffff;
    --wood-light: #e3b68c;
    --wood-mid: #d39e70;
    --wood-dark: #c58a5c;
    --ink-blue: #2b3990;
    --ink-body: #3b3431;
    --bullet-red: #d2232a;
    --crop: #231f20;
  }
  html, body { margin: 0; padding: 0; overflow: hidden; }
  body { width: 1031px; height: 1200px; background: var(--paper); position: relative; }
  .page { position: absolute; inset: 0; width: 1031px; height: 1200px; }
  .bleed-photo {
    position: absolute; left: 62px; top: 56px; width: 908px; height: 1091px;
    background: linear-gradient(135deg, var(--wood-light) 0%, var(--wood-mid) 55%, var(--wood-dark) 85%, #f0d2ab 100%);
  }
  .crop-marks { position: absolute; inset: 0; }
  .title {
    position: absolute; left: 62px; width: 908px; top: 104px; margin: 0;
    text-align: center; font: 700 51px/1 "Poppins", sans-serif; color: var(--ink-blue);
    -webkit-text-stroke: 5px #fff; paint-order: stroke fill; letter-spacing: 0.5px;
  }
  .outcome {
    position: absolute; left: 62px; width: 908px; top: 171px; margin: 0;
    text-align: center; font: 700 34px/43px "Poppins", sans-serif; color: var(--ink-blue);
    -webkit-text-stroke: 4px #fff; paint-order: stroke fill; white-space: nowrap;
  }
  .lead {
    position: absolute; left: 143px; margin: 0; white-space: nowrap;
    font: italic 900 28px/36px "Mulish", sans-serif; color: var(--ink-blue);
  }
  .body-text {
    position: absolute; left: 227px; margin: 0; white-space: nowrap;
    font: 400 38px/45px "Didact Gothic", sans-serif; color: var(--ink-body); letter-spacing: 0.5px;
  }
  .aims { position: absolute; left: 214px; top: 776px; margin: 0; padding: 0; list-style: none; }
  .aims li {
    position: relative; padding-left: 38px; margin: 0; white-space: nowrap;
    font: 400 34px/40px "Didact Gothic", sans-serif; color: var(--ink-body); letter-spacing: 0.8px;
  }
  .aims li::before {
    content: ""; position: absolute; left: 3px; top: 11px; width: 17px; height: 17px;
    background: var(--bullet-red); transform: rotate(45deg);
  }
  .page-number { position: absolute; left: 804px; top: 986px; width: 82px; height: 72px; }
</style>
</head>
<body>
<div class="page">
  <div class="bleed-photo" role="img" aria-label="Background photograph of diagonal light bamboo slats in warm natural tones"></div>

  <svg class="crop-marks" width="1031" height="1200" viewBox="0 0 1031 1200" aria-hidden="true">
    <g stroke="var(--crop)" stroke-width="1" fill="none">
      <path d="M62 0V36M86 0V56M0 56H40M0 71H62"/>
      <path d="M970 0V36M946 0V56M991 56H1031M970 71H1031"/>
      <path d="M62 1164V1200M86 1147V1200M0 1147H40M0 1128H62"/>
      <path d="M970 1164V1200M946 1147V1200M991 1147H1031M970 1128H1031"/>
    </g>
  </svg>

  <h1 class="title">3. Same Same Different</h1>
  <h2 class="outcome">EYLF – Outcome 2: Children are<br>connected with and contribute to their<br>world</h2>

  <p class="lead" style="top:313px">Children respond to diversity with respect when<br>they…</p>
  <p class="body-text" style="top:388px">notice and react in positive ways to<br>similarities and differences among<br>people</p>

  <p class="lead" style="top:522px">Educators promote this learning when they…</p>
  <p class="body-text" style="top:560px">plan experiences and provide<br>resources that broaden children’s<br>perspectives and encourage<br>appreciation of diversity</p>

  <p class="lead" style="top:738px">This task provides an opportunity to:</p>
  <ul class="aims">
    <li>explore the concepts<br>of “same” and “different”</li>
    <li>discuss diversity</li>
    <li>model and sort based<br>on specific criteria</li>
    <li>celebrate similarities<br>and differences</li>
  </ul>

  <svg class="page-number" viewBox="0 0 82 72" aria-label="Page 6">
    <polygon points="41,1 81,27 67,71 15,71 1,27" fill="var(--ink-blue)"/>
    <text x="41" y="50" text-anchor="middle" font-family="Didact Gothic, sans-serif" font-size="32" fill="#fff">6</text>
  </svg>
</div>
</body>
</html>
```